Business cards to launch an education platform

Hi,
I am looking at having new business cards designed.
I am a startup, developing a web platform for schools and university, the education world. It's an online assessment system.
I would like a card that looks classy, and that is using the colors and the font of my logo.

I have attached:
1) my logo
2) A business card that I have designed quickly so you can have all the information required in the card, but I really don't like it.
3) The font that I am using (Lato Regular) to design my web platform
4) Some screenshots of my web platform so you can have a look at the style that I have.

Target Market(s)

Major market: Education system: Schools and university
Minor markets: Business in general

Industry/Entity Type

Business

Contact Information for Business Card

Clara Fenwick
Director

M: 0437 518 902
E: clara.fenwick@amberLoomSystems.com.au

Requirements
Must have
• The colors of my logo

```html
<!DOCTYPE html>
<html lang="en">
<head>
<meta charset="utf-8">
<title>Amber Loom Systems – Business Cards</title>
<link rel="stylesheet" href="https://fonts.googleapis.com/css2?family=PT+Sans:wght@400;700&display=swap">
<style>
  :root {
    --backdrop: #e9ecf1;
    --paper: #ffffff;
    --navy: #0b3a7e;
    --navy-deep: #082c63;
    --blue: #1a5bb0;
    --cyan: #35c8f2;
    --cyan-soft: #7fdcf8;
    --ink-blue: #1f4f98;
  }
  * { box-sizing: border-box; margin: 0; padding: 0; }
  html, body { width: 1200px; height: 950px; overflow: hidden; }
  body {
    background: var(--backdrop);
    font-family: "PT Sans", Arial, sans-serif;
    display: flex;
    flex-direction: column;
    align-items: center;
    justify-content: center;
    gap: 50px;
  }
  .card {
    position: relative;
    width: 700px;
    height: 400px;
    overflow: hidden;
    box-shadow: 0 10px 24px rgba(10, 30, 70, 0.22);
  }

  /* Front */
  .card-front { background: var(--paper); }
  .front-band {
    position: absolute;
    left: 0; right: 0; bottom: 0;
    height: 190px;
    background: linear-gradient(180deg, var(--blue) 0%, var(--navy) 100%);
  }
  .front-divider {
    position: absolute;
    left: 0; top: 196px;
    width: 700px; height: 30px;
  }
  .brand {
    position: absolute;
    left: 210px; top: 80px;
    display: flex;
    align-items: center;
    gap: 18px;
  }
  .brand-square {
    width: 62px; height: 62px;
    background: var(--blue);
  }
  .brand-name {
    font-size: 34px;
    font-weight: 400;
    letter-spacing: 2px;
    color: var(--ink-blue);
    line-height: 1.1;
  }
  .contact {
    position: absolute;
    left: 0; right: 0; bottom: 42px;
    text-align: center;
    color: #ffffff;
  }
  .contact-name {
    font-size: 24px;
    font-weight: 700;
    letter-spacing: 0.5px;
  }
  .contact-role { font-weight: 400; font-size: 20px; }
  .contact-line {
    font-size: 17px;
    margin-top: 10px;
    color: #dbe8fb;
  }

  /* Back */
  .card-back {
    background: radial-gradient(ellipse at 75% 80%, var(--blue) 0%, var(--navy) 55%, var(--navy-deep) 100%);
    color: #ffffff;
  }
  .back-title {
    position: absolute;
    right: 60px; top: 50px;
    text-align: right;
    font-size: 32px;
    letter-spacing: 3px;
    color: var(--cyan-soft);
    line-height: 1.1;
  }
  .back-points {
    position: absolute;
    left: 60px; top: 60px;
    list-style: none;
    font-size: 18px;
    color: var(--cyan-soft);
    line-height: 1.6;
  }
  .back-points li::before {
    content: "";
    display: inline-block;
    width: 7px; height: 7px;
    border-radius: 50%;
    background: var(--cyan);
    margin-right: 10px;
    vertical-align: middle;
  }
  .back-web {
    position: absolute;
    left: 60px; bottom: 50px;
    font-size: 17px;
    color: var(--cyan-soft);
  }
  .back-square {
    position: absolute;
    right: 80px; bottom: 60px;
    width: 170px; height: 170px;
    background: linear-gradient(135deg, var(--cyan) 0%, var(--blue) 100%);
    opacity: 0.55;
  }
</style>
</head>
<body>

  <section class="card card-front">
    <div class="brand">
      <span class="brand-square"></span>
      <span class="brand-name">AMBER LOOM SYSTEMS</span>
    </div>
    <div class="front-band"></div>
    <svg class="front-divider" viewBox="0 0 700 30" aria-hidden="true">
      <polyline points="0,6 540,6 552,18 574,18 586,6 700,6" fill="none" stroke="var(--cyan)" stroke-width="5"/>
    </svg>
    <div class="contact">
      <p class="contact-name">CLARA FENWICK <span class="contact-role">- DIRECTOR</span></p>
      <p class="contact-line">0437 518 902</p>
      <p class="contact-line">clara.fenwick@amberLoomSystems.com.au</p>
    </div>
  </section>

  <section class="card card-back">
    <ul class="back-points">
      <li>Lorem ipsum dolor</li>
      <li>Wisi mandamus</li>
      <li>Vix cu discere</li>
    </ul>
    <p class="back-title">AMBER LOOM<br>SYSTEMS</p>
    <span class="back-square"></span>
    <p class="back-web">www.amberLoomSystems.com.au</p>
  </section>

</body>
</html>
```